Ridge Lass Crew (Flyer)

I want a flyer to advertise my service.
Details below, and logo's to use are attached.

A girls only after school program, 11-14yrs, as OSHC is no longer avail, dedicated to coaching & mentoring our girls into strong, independent young women.

The Brainchild of Rebecca Folwin, Ridge Lass Crew was created to address the growing demand for after school/school holiday supervision for kids moving from primary into high school, when OSHC ceases to exist.
With over 12 years experience mentoring and coaching young women in the corporate world, Bec decided to leave her role as a Director with Tarrant Trust, and follow her passion.
Bec, along with her sister Lorraine, who has over 10 years experience in local communities as a Youth Worker, and is also a qualified Enrolled Nurse, embarked on building a program designed to keep parents happy (by knowing their girls are safe) and dedicated to coaching and mentoring our girls into strong, independent young women.
Open every afternoon and during school holidays, we look to offer;
- Daily meditation
- Healthy snacks
- Dedicated homework time
- Organised group activity, led by qualified instructors (yoga, fitness class, soccer etc)
- Regular guests speakers, addressing issues/concerns for young people today
- SOCIAL MEDIA FREE ZONE

Located 87 Pelham Pde, Baulkham Hills (across from Crestmoor Day Clinic)
Open 3-6pm Monday to Friday

Facebook page: http://fb.example/ridgelasscrew
Email: info@ridgelasscrew.example.au
Mobile: 0455817396

Target Market(s)

Parents of teenage girls, teenage girls 11-14 years

Industry/Entity Type

School

Font styles to use
Sans Serif

Colors
b768aa
e667a6

Requirements
Must have
• What progam is - see brief
• Who runs it
Should not have
• Not be too busy, not overly mature images

```html
<!DOCTYPE html>
<html lang="en">
<head>
<meta charset="utf-8">
<title>Ridge Lass Crew – After School Program Flyer</title>
<link rel="stylesheet" href="https://fonts.googleapis.com/css2?family=Carlito:wght@400;700&family=Cinzel:wght@400;700&family=Oswald:wght@300&family=Courier+Prime:wght@700&family=Roboto+Condensed:wght@400;700&display=swap">
<style>
  :root {
    --pink: #e667a6;
    --pink-deep: #e04d95;
    --purple: #b768aa;
    --lavender: #d9d3ea;
    --ink: #1c1420;
    --slate: #3b3744;
    --white: #ffffff;
    --footer-bg: #fbf4f8;
  }
  html, body { margin: 0; padding: 0; overflow: hidden; background: #ffffff; }
  .flyer {
    position: relative;
    width: 848px;
    height: 1200px;
    overflow: hidden;
    background: var(--white);
    font-family: "Carlito", "Calibri", sans-serif;
  }
  .backdrop { position: absolute; inset: 0; }
  .flyer > div, .flyer > p, .flyer > h1, .flyer > h2, .flyer > ul { position: absolute; margin: 0; }

  .brand-mark {
    left: 600px; top: 40px; width: 232px; height: 220px;
    display: flex; align-items: center; justify-content: center; text-align: center;
    color: var(--pink-deep); font-weight: 700; font-size: 46px; line-height: 1.0;
  }
  .headline {
    right: 22px; top: 318px; width: 340px; text-align: center;
    color: var(--pink-deep); font-weight: 700; font-size: 40px; line-height: 56px;
    white-space: nowrap;
  }
  .age-band { left: 436px; top: 458px; width: 400px; }
  .age-band .ages {
    font-family: "Cinzel", serif; font-weight: 700; font-size: 30px; color: var(--ink);
    letter-spacing: 0.5px;
  }
  .age-band .reason {
    position: absolute; right: 6px; top: 46px; white-space: nowrap;
    font-family: "Carlito", sans-serif; font-size: 20px; color: var(--ink); letter-spacing: 1.2px;
  }
  .section-title-about {
    left: 64px; top: 598px;
    font-family: "Oswald", sans-serif; font-weight: 300; font-size: 26px; color: var(--white);
  }
  .about-text {
    left: 27px; top: 664px; width: 405px;
    font-size: 22px; line-height: 28.8px; color: var(--white);
  }
  .section-title-offer {
    left: 544px; top: 597px;
    font-weight: 700; font-size: 24px; letter-spacing: 0.6px; color: var(--slate);
  }
  .offer-list { left: 516px; top: 0; padding: 0; list-style: none; }
  .offer-list li {
    position: absolute; left: 0; white-space: nowrap;
    font-size: 21px; color: var(--slate); display: flex; align-items: flex-start; gap: 12px;
  }
  .offer-list li svg { flex: none; margin-top: 3px; }
  .offer-list .sub { display: block; padding-left: 10px; }
  .founder-line {
    left: 0; width: 872px; top: 940px; text-align: center;
    font-family: "Cinzel", serif; font-weight: 700; font-size: 23px; color: var(--ink);
  }
  .program-name {
    left: 0; width: 872px; top: 976px; text-align: center;
    font-family: "Cinzel", serif; font-weight: 400; font-size: 36px; letter-spacing: 2px; color: var(--ink);
  }
  .mission {
    left: 0; width: 868px; text-align: center;
    font-family: "Courier Prime", monospace; font-weight: 700; font-size: 17px;
    font-variant: small-caps; letter-spacing: 2.4px; color: var(--white);
  }
  .mission-1 { top: 1046px; }
  .mission-2 { top: 1082px; }
  .contact-web { left: 22px; top: 1126px; width: 250px; font-size: 17px; color: var(--ink); line-height: 24px; }
  .contact-web .email-label { display: flex; justify-content: flex-end; align-items: center; gap: 6px; padding-right: 14px; }
  .contact-web .social { display: flex; align-items: center; gap: 6px; }
  .contact-phone {
    left: 310px; top: 1152px;
    font-family: "Roboto Condensed", sans-serif; font-size: 22px; color: var(--ink); letter-spacing: 0.4px;
  }
  .contact-address {
    left: 578px; top: 1150px; display: flex; align-items: center; gap: 6px;
    font-family: "Roboto Condensed", sans-serif; font-weight: 700; font-size: 19px; color: var(--white);
    letter-spacing: -0.3px; white-space: nowrap;
  }
</style>
</head>
<body>
<main class="flyer">
  <svg class="backdrop" width="848" height="1200" viewBox="0 0 848 1200" aria-hidden="true">
    <defs>
      <linearGradient id="photoTone" x1="0" y1="0" x2="1" y2="1">
        <stop offset="0" stop-color="#c9c6c4"/>
        <stop offset="0.45" stop-color="#eeeeef"/>
        <stop offset="1" stop-color="#d7d2d2"/>
      </linearGradient>
      <linearGradient id="pinkBody" x1="0" y1="0" x2="1" y2="0">
        <stop offset="0" stop-color="#e05ba0"/>
        <stop offset="1" stop-color="#dc66a6"/>
      </linearGradient>
    </defs>
    <path d="M0 0 H490 C518 150 505 335 448 438 L848 438 L848 1200 H0 Z" fill="url(#pinkBody)"/>
    <path d="M448 438 H848 V544 H340 Z" fill="var(--purple)"/>
    <path d="M0 1142 C350 1138 650 1130 848 1052 V1200 H0 Z" fill="var(--footer-bg)"/>
    <path d="M848 1042 C720 1092 570 1128 480 1200 H848 Z" fill="var(--purple)"/>
  </svg>

  <svg class="backdrop" width="848" height="1200" viewBox="0 0 848 1200">
    <path role="img" aria-label="Photo of a girl wearing a white program T-shirt"
          d="M0 0 H455 C482 150 470 360 405 448 C335 530 180 560 0 554 Z" fill="url(#photoTone)"/>
  </svg>

  <svg class="backdrop" width="848" height="1200" viewBox="0 0 848 1200" aria-hidden="true">
    <circle cx="716" cy="150" r="116" fill="var(--lavender)" opacity="0.45"/>
  </svg>
  <div class="brand-mark">Ridge Lass Crew</div>

  <h1 class="headline">A Girls Only After<br>School Program</h1>

  <div class="age-band">
    <div class="ages">For 11-14yrs</div>
    <div class="reason">as OSHC is no longer available</div>
  </div>

  <h2 class="section-title-about">ABOUT US</h2>
  <p class="about-text">The Brainchild of Rebecca Folwin, Ridge Lass Crew was created to address the growing demand for after school/school holiday supervision for kids moving from primary into high school, when OSHC ceases to exist.</p>

  <h2 class="section-title-offer">WHAT WE OFFER</h2>
  <ul class="offer-list">
    <li style="top:646px"><svg width="16" height="16" viewBox="0 0 16 16"><circle cx="8" cy="8" r="6.5" fill="none" stroke="var(--white)" stroke-width="2"/><path d="M5 8.2 L7.2 10.3 L11 6" fill="none" stroke="var(--white)" stroke-width="2"/></svg>Daily meditation</li>
    <li style="top:686px"><svg width="16" height="16" viewBox="0 0 16 16"><circle cx="8" cy="8" r="6.5" fill="none" stroke="var(--white)" stroke-width="2"/><path d="M5 8.2 L7.2 10.3 L11 6" fill="none" stroke="var(--white)" stroke-width="2"/></svg>Healthy snacks</li>
    <li style="top:731px"><svg width="16" height="16" viewBox="0 0 16 16"><circle cx="8" cy="8" r="6.5" fill="none" stroke="var(--white)" stroke-width="2"/><path d="M5 8.2 L7.2 10.3 L11 6" fill="none" stroke="var(--white)" stroke-width="2"/></svg><span>Organised group activity,<span class="sub">(yoga, fitness class, soccer etc.)</span></span></li>
    <li style="top:784px"><svg width="16" height="16" viewBox="0 0 16 16"><circle cx="8" cy="8" r="6.5" fill="none" stroke="var(--white)" stroke-width="2"/><path d="M5 8.2 L7.2 10.3 L11 6" fill="none" stroke="var(--white)" stroke-width="2"/></svg>Regular guests speakers</li>
    <li style="top:834px"><svg width="16" height="16" viewBox="0 0 16 16"><circle cx="8" cy="8" r="6.5" fill="none" stroke="var(--white)" stroke-width="2"/><path d="M5 8.2 L7.2 10.3 L11 6" fill="none" stroke="var(--white)" stroke-width="2"/></svg>Dedicated homework time</li>
    <li style="top:880px"><svg width="16" height="16" viewBox="0 0 16 16"><circle cx="8" cy="8" r="6.5" fill="none" stroke="var(--white)" stroke-width="2"/><path d="M5 8.2 L7.2 10.3 L11 6" fill="none" stroke="var(--white)" stroke-width="2"/></svg>Social media free zone</li>
  </ul>

  <p class="founder-line">The Brainchild of Rebecca Folwin</p>
  <p class="program-name">Ridge Lass Crew</p>
  <p class="mission mission-1">Dedicated to Coaching &amp; Mentoring Our Girls</p>
  <p class="mission mission-2">into Strong, Independent Young women</p>

  <div class="contact-web">
    <div class="email-label">e-Mail us
      <svg width="18" height="16" viewBox="0 0 18 16"><rect x="1.5" y="3" width="15" height="11" fill="none" stroke="var(--ink)" stroke-width="1"/><path d="M1.5 3 L9 9.5 L16.5 3 M1.5 14 L7 8 M16.5 14 L11 8" fill="none" stroke="var(--ink)" stroke-width="1"/></svg>
    </div>
    <div>info@ridgelasscrew.example.au</div>
    <div class="social">http://fb.example/ridgelasscrew <svg width="16" height="16" viewBox="0 0 16 16"><circle cx="8" cy="8" r="8" fill="var(--ink)"/></svg></div>
  </div>

  <div class="contact-phone">CALL US: 0455817396</div>

  <div class="contact-address">
    <svg width="22" height="30" viewBox="0 0 22 30"><path d="M11 1 C5 1 1 5.5 1 11 C1 18 11 29 11 29 C11 29 21 18 21 11 C21 5.5 17 1 11 1 Z" fill="var(--white)"/><circle cx="11" cy="11" r="4" fill="var(--purple)"/></svg>
    87 Pelham Pde, Baulkham Hills
  </div>
</main>
</body>
</html>
```